Website for Reiki and Wellness Courses

I teach online courses in Reiki and wellness/self-development and am needing a new website.

The focus of the website will be to provide descriptions of the courses as well as include a blog and pages where students in my courses will visit for additional information.

Note: courses are NOT hosted on this site.
The focus of this website will be to encourage viewers to enroll in courses as well as opt in to the email list.

I will upload copy soon. My old website is: http://brightfernstudies.example. Please do not use existing logo.

Target Market(s)

Alternative health, wellness, spirituality, personal development. Males and females of all ages seeking to improve their health and life.

Industry/Entity Type

Health And Wellness

Logo Text

No text (please do not use existing logo)

Coding

Coded - Design and coding required

Number of Pages Required

5+ page

Requirements
Must have
• 1. Home page
• 2. About page
• 3. Courses page that outlines courses (there are currently 6 courses with 1 coming soon)
• 4. Individual course page (maybe a template that I can adjust color and pictures for with each course)
• 5. Blog
• 6. Student Area that outlines all Student Areas
• 7. Individual Student Area page (maybe a template that I can adjust color and pictures for with each course)
• 8. Shop page (note: items will not currently be purchased through website - it will be a link to quillmarket for a book).
• 9. Student thank-you page (maybe a template that I can adjust color and pictures for with each course) this is the page students are directed to at end of course with vouchers for other courses.
• Opt-in for the home page, course pages, blog and thank-you pages
Nice to have
• I would like the design to be calm, clean and soothing. Ideally visitors feel relaxed when viewing the site and are encouraged to explore the courses, subscribe to the email list and purchase a product.
• ~ Testimonials page
• ~ Contact page
• I tend to gravitate towards blues, greys and purples as well as monochromatic color schemes.
Should not have
• Contact form on home page
• phone number on home page
• location/physical address
• dates for blog posts

```html
<!DOCTYPE html>
<html lang="en">
<head>
<meta charset="utf-8">
<title>Bright Fern Studies</title>
<link href="https://fonts.googleapis.com/css2?family=Raleway:wght@400;600;700;800&family=Open+Sans:wght@400;600&display=swap" rel="stylesheet">
<style>
:root{
  --accent:#c4343a;
  --ink:#3d3d42;
  --muted:#6d6d73;
  --slate:#5c5c63;
  --charcoal:#48484e;
  --footer:#55555c;
  --light:#f4f4f5;
  --line:#dcdcde;
  --white:#ffffff;
  --sand:#d8d1c5;
  --sand-deep:#a9a398;
}
*{box-sizing:border-box;margin:0;padding:0}
html,body{width:732px;height:1200px;overflow:hidden}
body{font-family:"Open Sans",Arial,sans-serif;color:var(--ink);background:var(--white);font-size:7px;line-height:1.5}
h1,h2,h3,.brand,.nav a,.btn{font-family:"Raleway",Arial,sans-serif}

.site-header{height:50px;background:var(--light);display:flex;align-items:center;justify-content:space-between;padding:0 34px;border-bottom:1px solid var(--line)}
.brand{display:flex;align-items:center;gap:8px;font-size:15px;font-weight:600;color:var(--slate)}
.brand-mark{width:24px;height:24px;background:var(--slate)}
.nav{display:flex;align-items:center;gap:16px}
.nav a{font-size:7.5px;font-weight:700;color:var(--ink);text-decoration:none;letter-spacing:.5px}
.nav .search{width:18px;height:18px;background:var(--slate);display:flex;align-items:center;justify-content:center}

.hero{position:relative;height:401px}
.hero-photo{position:absolute;inset:0;background:linear-gradient(100deg,var(--sand) 0%,#cdc6b9 45%,#8f8b86 75%,var(--sand-deep) 100%)}
.hero-panel{position:absolute;left:36px;top:80px;width:238px;height:190px;background:rgba(70,70,76,.85);padding:20px 18px;color:var(--white)}
.hero-panel h1{font-size:19px;font-weight:800;line-height:1.15;letter-spacing:.3px}
.hero-panel p{font-size:8px;margin-top:10px;line-height:1.45;color:#ececec}
.btn{display:inline-block;background:var(--accent);color:var(--white);font-weight:700;font-size:7px;padding:7px 12px;margin-top:14px;letter-spacing:.6px;text-decoration:none}
.dots{position:absolute;bottom:14px;left:50%;transform:translateX(-50%);display:flex;gap:6px}
.dots span{width:7px;height:7px;border-radius:50%;border:1px solid var(--white)}
.dots .on{background:var(--accent);border-color:var(--accent)}

.about{height:249px;padding:16px 70px 0;text-align:center}
.section-title{font-size:21px;font-weight:800;color:var(--accent);letter-spacing:.5px}
.about-icon{margin:4px auto 6px;display:block}
.about-text{font-size:6.5px;color:var(--muted);max-width:560px;margin:0 auto}
.cards{display:flex;gap:18px;margin-top:14px}
.card{flex:1;text-align:center}
.card-photo{height:54px;position:relative}
.card-photo .tag{position:absolute;right:0;bottom:0;background:var(--charcoal);color:var(--white);font-size:5px;padding:2px 6px;font-family:"Raleway",sans-serif;font-weight:700}
.card h3{font-size:9.5px;color:var(--accent);font-weight:700;margin-top:6px;line-height:1.2}
.card p{font-size:5.5px;color:var(--muted);margin-top:3px}

.testimonials{position:relative;height:195px;background:linear-gradient(90deg,#5a5a60,#6a6a70 50%,#505056);text-align:center;color:var(--white);padding:20px 90px}
.testimonials .section-title{color:var(--white)}
.quote-head{font-family:"Raleway",sans-serif;font-weight:700;font-size:8px;margin-top:10px;letter-spacing:.3px}
.quote{font-size:6px;color:#e6e6e6;margin-top:6px}
.author{font-size:8.5px;margin-top:8px;font-weight:600}
.arrow{position:absolute;top:88px;width:14px;height:14px;border-radius:50%;background:var(--white);display:flex;align-items:center;justify-content:center}
.arrow.left{left:30px}.arrow.right{right:30px}

.inspire{height:190px;text-align:center;padding:26px 120px 0}
.inspire-text{font-size:6.5px;color:var(--muted);margin-top:8px}
.optin{display:flex;gap:10px;justify-content:center;margin-top:14px}
.optin span{width:98px;height:18px;border:1px solid var(--line);background:var(--light);font-size:6px;color:var(--muted);text-align:left;padding:3px 6px}
.btn.dark{background:var(--slate);font-size:8px;padding:7px 22px;margin-top:14px}

.site-footer{height:115px;background:var(--footer);color:var(--white);text-align:center;padding-top:20px}
.site-footer .nav{justify-content:center}
.site-footer .nav a{color:var(--white);font-size:6.5px}
.social{display:flex;gap:7px;justify-content:center;margin-top:12px}
.social span{width:11px;height:11px;border-radius:50%;background:var(--white);opacity:.9}
.copy{font-size:5.5px;margin-top:12px;color:#d8d8d8}
</style>
</head>
<body>
<header class="site-header">
  <div class="brand"><span class="brand-mark"></span>Bright Fern Studies</div>
  <nav class="nav">
    <a href="#">HOME</a><a href="#">ABOUT</a><a href="#">COURSES</a><a href="#">BLOG</a><a href="#">STUDENT AREAS</a><a href="#">CONTACT</a>
    <span class="search"><svg width="9" height="9" viewBox="0 0 10 10"><circle cx="4" cy="4" r="3" fill="none" stroke="#fff" stroke-width="1.3"/><line x1="6.2" y1="6.2" x2="9" y2="9" stroke="#fff" stroke-width="1.3"/></svg></span>
  </nav>
</header>

<section class="hero">
  <div class="hero-photo" role="img" aria-label="Hero photo: a dark smooth stone resting on raked zen sand"></div>
  <div class="hero-panel">
    <h1>BECOME A CERTIFIED USUI REIKI MASTER</h1>
    <p>This comprehensive online course gives you all of the tools you need to be certified as a Traditional Usui Reiki Master.</p>
    <a class="btn" href="#">LEARN MORE ›</a>
  </div>
  <div class="dots"><span></span><span class="on"></span><span></span></div>
</section>

<section class="about">
  <h2 class="section-title">ABOUT US</h2>
  <svg class="about-icon" width="22" height="16" viewBox="0 0 22 16"><rect x="3" y="1" width="16" height="11" fill="none" stroke="#6d6d73" stroke-width="1.4"/><rect x="0" y="13" width="22" height="2" fill="#6d6d73"/></svg>
  <p class="about-text">Thought to be centuries old and rediscovered in the late 1800s, Reiki is a gentle practice of healing and quiet renewal. Its name joins two words meaning universal life energy. As a practitioner of Reiki, you become a channel for this energy and share it for the physical and emotional healing of self and others. Reiki is non-denominational and can be practised by anyone, regardless of their religion and spiritual beliefs, and it may be given in person or from a distance.</p>
  <div class="cards">
    <div class="card">
      <div class="card-photo" role="img" aria-label="Hands resting gently during a Reiki session" style="background:linear-gradient(135deg,#8d8d93,#b7b3ad)"><span class="tag">MORE</span></div>
      <h3>How Reiki Works</h3>
      <p>Reiki has been used for centuries to help individuals with physical and emotional imbalances.</p>
    </div>
    <div class="card">
      <div class="card-photo" role="img" aria-label="Calm treatment room with soft light" style="background:linear-gradient(135deg,#6f6f75,#a7a39d)"><span class="tag">MORE</span></div>
      <h3>Traditional Usui Reiki<br>Master Certification</h3>
      <p>Learn how to use Reiki to help yourself and others.</p>
    </div>
    <div class="card">
      <div class="card-photo" role="img" aria-label="Open notebook and books on a desk" style="background:linear-gradient(135deg,#7c7c82,#c2beb8)"><span class="tag">MORE</span></div>
      <h3>Resources</h3>
      <p>Information and tools to help you create a life you love.</p>
    </div>
  </div>
</section>

<section class="testimonials" role="img" aria-label="Muted grey background of a peaceful landscape">
  <h2 class="section-title">TESTIMONIALS</h2>
  <p class="quote-head">THIS COURSE CHANGED MY LIFE IN WONDERFUL WAYS!</p>
  <p class="quote">I came to this course with little idea of what to expect, and I left with a calmer mind and a deeper sense of purpose. The lessons were clear, warm and easy to follow at my own pace, and every module built gently on the last. I now share Reiki with my family and friends every week, and I feel more grounded and hopeful than I have in years. Thank you for such a caring and thoughtful course.</p>
  <p class="author">Dana Whitlow</p>
  <span class="arrow left"><svg width="6" height="6" viewBox="0 0 6 6"><path d="M4 0.5 1.5 3 4 5.5" fill="none" stroke="#55555c" stroke-width="1.2"/></svg></span>
  <span class="arrow right"><svg width="6" height="6" viewBox="0 0 6 6"><path d="M2 0.5 4.5 3 2 5.5" fill="none" stroke="#55555c" stroke-width="1.2"/></svg></span>
</section>

<section class="inspire">
  <h2 class="section-title">STAY INSPIRED</h2>
  <p class="inspire-text">Receive information and articles each month to keep you feeling inspired. As a thank you, you will also receive access to exciting news you can download for use in your Reiki practice and meditation.</p>
  <div class="optin"><span>First Name</span><span>Last Name</span><span>Email Address</span></div>
  <a class="btn dark" href="#">Yes - Count me in</a>
</section>

<footer class="site-footer">
  <nav class="nav"><a href="#">HOME</a><a href="#">ABOUT</a><a href="#">COURSES</a><a href="#">BLOG</a><a href="#">STUDENT AREAS</a><a href="#">CONTACT</a></nav>
  <div class="social"><span></span><span></span><span></span></div>
  <p class="copy">© 2024 brightfernstudies.example · All rights reserved</p>
</footer>
</body>
</html>
```